Hurricane Damage Public Adjuster Billboard

I have created several projects with you and have several great designs. I need to format them into a Billboard for upcoming Hurricane Season. Need done in a month. Im also in process of getting an eye catching and easy to remember 800# Vanity phone number like Call 800-Stormsafe or 800- Need Fix? My included past Craft Huddle projects will give you an idea of what colors, schemes, and designs I gravitate towards. 3 past Design projects were 1) 2 Logos where I picked the 1st place and the 2nd place and 2) Index Card where I picked the winner as the Index Card and the 2nd place as a Post Card. Point is, I will pick and pay for 2 winners if they're good. This should help to sweeten the pot. Also, please look at my website for ideas that I like:

www.TheClaimKeeperGroup.com
I want people to feel that I am the best and highest. Level.

I've been getting a lot of quick half effort designs basically cut & pasting my previous projects. Please don't rush and take your time to be creative. A an example, my Biggest Competitor is Vesta Public Adjusting. Their colors are Black and Gold while mine are Blue, White, and Black with a highlight of Orange if possible. I JUST imported a picture of their BillBoard. I need mine better and BLOW AWAY THEIRS. Terms like "Don't be Victimized Twice ?, Don't let the Hurricane Ruin your Life?". "Get Fairly Paid & Move On" "Our Clients Claims are VIP?
Updates

I'm getting a lot of quick half effort ones. I'd rather you take your time and really put some thoughts and effort into it. My Biggest Competitor is Vesta Public Adjusting. They have black & gold colors, while I have Blue, Black, and white.

It needs to blow theirs away. I have imported their Billboard for comparative purposes.

Guy's,
I'll make it easier for you in what I'm looking for. Please look at the Vesta Billboard picture attached.

1) Put my "Blue Shield" to the left, replacing their logo
2) change color patterns from their (Black, Gold, White) to my color schemes of (Black, Blue, White)
3) I want to see my name where their is:

THE
Claim Keeper's Group
EXPERT & LOCAL Public Adjusters
"FOR THE POLICYHOLDER!!"

4) to the right, add the A+Rated logo and QRS+ Accredited logo, 5 Star Zorbix Rated logo, 5 Start PORCHLINE Highly Rated logo, etc..

5) the right side is where you can be creative as I will not have a picture of me there.

"20+ Years of Experience, Recovering Millions for our VIP Clients"

"Your Best, Locally-Based Private Adjuster & Advocate'
"FOR THE POLICYHOLDER!!"

"Don't be victimized Twice!!"

"Don't let the Hurricane Ruin Your Life!!"

This should really help. Also, refer to my website, maybe a couple testimonial fillers?

Thanks all,

marcus@TheClaimKeeperGroup.com

Just imported a few awards that would look great to the right side with all the other 5 Star Ratings and accolades.
This right section could be titled like zmy Website:

5 Star Reviews, Ratings & Awards:
4-5 Logos underneath?

Target Market(s)

Coastal place where a Hurricane 🌀 🌀 Hits

Industry/Entity Type

Hurricane Public Insurance Adjuster

Font styles to use
Sans Serif
Other font styles liked:
• Zurich fonts

Colors
0054AA
0677BA
7BADD7
CADEEF
E8F1F8
EE7325
F08F49
F5BC92
FAE3D3
FDF4ED

Requirements
Must have
• Use my past project logos, colors, and schemes to create eye grabbing BillBoard
Nice to have
Should not have
• Not be too busy, must be Easy to Read, Eye Catchy

```html
<!DOCTYPE html>
<html lang="en">
<head>
<meta charset="utf-8">
<title>Claim Keeper's Group Hurricane Billboard</title>
<link rel="stylesheet" href="https://fonts.googleapis.com/css2?family=Bowlby+One&family=Poppins:wght@500;600;700;800&display=swap">
<style>
  :root{
    --sky-blue:#0a7ccc;
    --deep-blue:#0659a6;
    --navy:#0b1f4d;
    --night:#0a1a3f;
    --orange:#f58a0a;
    --white:#ffffff;
    --ink:#111111;
    --red:#e0262a;
    --green:#5bbf2a;
    --badge-blue:#1f5f8f;
    --star:#f5b400;
  }
  html,body{margin:0;padding:0;width:1099px;height:1200px;overflow:hidden;background:var(--white);}
  .billboard{
    position:absolute;left:20px;top:446px;width:1060px;height:308px;overflow:hidden;
    background:linear-gradient(100deg,var(--deep-blue) 0%,var(--sky-blue) 45%,var(--deep-blue) 100%);
    box-shadow:8px 10px 14px rgba(0,0,0,.35);
    font-family:'Poppins',sans-serif;
  }
  .orange-band{position:absolute;left:0;top:205px;width:100%;height:103px;background:var(--orange);}
  .brand-panel{position:absolute;left:0;top:0;width:300px;height:308px;}
  .brand-name{
    position:absolute;left:22px;top:110px;width:190px;text-align:center;
    font-family:'Poppins',sans-serif;font-weight:800;font-size:24px;line-height:1.15;color:var(--white);
  }
  .headline{
    position:absolute;left:316px;top:22px;margin:0;
    font-family:'Bowlby One',sans-serif;font-weight:400;font-size:45px;line-height:53px;color:var(--white);letter-spacing:.5px;
  }
  .tagline{
    position:absolute;left:828px;top:24px;margin:0;
    font-weight:800;font-size:14.5px;line-height:17px;color:var(--white);text-transform:uppercase;
  }
  .ratings-card{
    position:absolute;left:832px;top:110px;width:195px;height:95px;background:var(--white);border-radius:5px 5px 0 0;
  }
  .rating-aplus{position:absolute;left:16px;top:10px;width:80px;text-align:center;color:var(--red);font-weight:600;font-size:15px;line-height:16px;}
  .rating-aplus small{display:block;color:var(--ink);font-family:Georgia,serif;font-size:6.5px;line-height:7px;font-weight:400;}
  .rating-zorbix{position:absolute;left:112px;top:8px;width:72px;text-align:center;color:var(--sky-blue);font-weight:600;font-size:19px;line-height:20px;}
  .stars{display:block;color:var(--star);font-size:9px;letter-spacing:1px;line-height:10px;}
  .rating-porchline{position:absolute;left:10px;top:57px;color:var(--green);font-weight:600;font-size:13px;}
  .accredit-badge{position:absolute;left:107px;top:55px;width:66px;height:26px;background:var(--badge-blue);border-radius:3px;}
  .award-badge{position:absolute;left:313px;top:228px;width:54px;height:60px;border-radius:6px;
    background:linear-gradient(160deg,#3b4f8a,#b02236 55%,#c9ced6);}
  .call{position:absolute;left:386px;top:222px;width:262px;color:var(--ink);}
  .call-label{display:block;font-weight:500;font-size:30px;line-height:30px;}
  .call-number{display:flex;align-items:center;gap:3px;font-weight:700;font-size:31px;line-height:38px;letter-spacing:-0.8px;white-space:nowrap;}
  .call-number svg{flex:none;}
  .experience{position:absolute;left:658px;top:212px;display:flex;align-items:flex-start;color:var(--white);}
  .experience-number{font-weight:600;font-size:30px;line-height:34px;}
  .experience-number sup{font-size:13px;}
  .experience-text{margin-left:4px;padding-top:4px;}
  .experience-years{display:block;font-weight:600;font-size:10.5px;letter-spacing:3px;line-height:12px;}
  .experience-claim{display:block;color:var(--ink);font-weight:700;font-size:13.5px;line-height:16px;}
  .web-bar{position:absolute;left:662px;top:254px;width:398px;height:35px;background:var(--navy);border-radius:5px 0 0 5px;
    display:flex;align-items:center;padding-left:20px;box-sizing:border-box;color:var(--white);font-weight:500;font-size:15.5px;letter-spacing:2.4px;}
  .web-bar .domain{color:var(--sky-blue);font-weight:600;}
</style>
</head>
<body>
<section class="billboard">
  <div class="orange-band"></div>

  <svg class="brand-panel" viewBox="0 0 300 308" role="img" aria-label="Stormy night field with a dirt road under a dark blue sky">
    <defs>
      <linearGradient id="stormSky" x1="0" y1="0" x2="0.6" y2="1">
        <stop offset="0" stop-color="#0a1f57"/>
        <stop offset="0.5" stop-color="#0d2f7a"/>
        <stop offset="1" stop-color="#071636"/>
      </linearGradient>
    </defs>
    <path d="M0 0 H286 C292 120 262 232 152 308 H0 Z" fill="url(#stormSky)"/>
    <path d="M150 0 H280 Q291 0 291 14 C288 130 258 232 152 308" fill="none" stroke="#f58a0a" stroke-width="4"/>
  </svg>
  <div class="brand-name">Claim Keeper's Group</div>

  <h1 class="headline">DON'T LET THE<br>HURRICANE<br>RUIN YOUR LIFE!!</h1>

  <p class="tagline">Your best, local<br>based private<br>adjuster &amp; advocate<br>for the policyholder!!</p>

  <div class="ratings-card">
    <div class="rating-aplus">A+ Rating<small>Highest Rating For<br>Public Insurance Adjusters<br>(Source: Review Index)</small></div>
    <div class="rating-zorbix">Zorbix<span class="stars">★★★★★</span></div>
    <div class="rating-porchline">PORCHLINE</div>
    <div class="accredit-badge"></div>
  </div>

  <div class="award-badge"></div>
  <div class="call">
    <span class="call-label">Call</span>
    <span class="call-number">
      <svg width="24" height="24" viewBox="0 0 24 24" aria-hidden="true">
        <circle cx="12" cy="12" r="11" fill="#0b1f4d"/>
        <path d="M8.2 6.5c.6-.4 1.3-.2 1.6.4l.9 1.8c.3.6.1 1.2-.4 1.6l-.7.5c.6 1.5 1.7 2.7 3.2 3.4l.5-.7c.4-.5 1-.7 1.6-.4l1.8.9c.6.3.8 1 .4 1.6l-.6.9c-.5.8-1.5 1.1-2.4.8-3.4-1.2-5.9-3.8-7.1-7.1-.3-.9 0-1.9.8-2.4z" fill="#fff"/>
      </svg>850-555-0147
    </span>
  </div>

  <div class="experience">
    <span class="experience-number">20<sup>+</sup></span>
    <span class="experience-text">
      <span class="experience-years">YEARS OF EXPERIENCE</span>
      <span class="experience-claim">RECOVERING MILLIONS FOR OUR VIP CLIENTS</span>
    </span>
  </div>

  <div class="web-bar">www.<span class="domain">theclaimkeepergroup</span>.com</div>
</section>
</body>
</html>
```